BrivoNest Learning App for Children with Dyslexia

Project Description:

We are seeking a talented UI/UX designer to create engaging and intuitive designs for Brivonest, an innovative educational app designed to help children learn letters and words through a multisensory learning approach. The app aims to be particularly helpful for children with dyslexia, providing a supportive and interactive learning environment.

Key App Features & Design Requirements:

Account Creation Screen: Design a welcoming and straightforward sign-up page that allows users to register with their email or continue with Quarnix. The design should be clean, focusing on user-friendliness and accessibility, adhering to our terms of service and privacy policy.

Main Screen Design: The main screen should allocate at least 4/6 of its height to the interactive drawing area. It needs to display word prompts in both correct and scrambled orders and include options to "Show all Words," "Play all words," and a search function. The interface should be vibrant, engaging, and easy to navigate for children.

Profile Section: Create a user-friendly profile page that allows users to edit their profile image, name, username, email, links, and bio. The design should be clean and encourage user engagement.

BrivoTally Page: This section will display the user's learning progress, including rankings, a learning curve, and recently learned words. It should visually represent progress in a motivating and understandable way, suitable for a younger audience.

Visual and Auditory Feedback Implementation: Incorporate elements that support visual and auditory feedback, using dyslexia-friendly formats. This includes choosing appropriate colors, fonts, and auditory cues.

Accessibility and Customization Settings: Designs should include settings for adjusting visual contrast, font size, and the word list to accommodate individual preferences and needs.

Feel free to add more interactions and/or pages.

Design preferences:

Color Scheme: Use a bright, inviting color palette that stimulates learning and engagement without overwhelming the users.
Font Selection: Opt for fonts that are readable and accessible, particularly for users with dyslexia.
Icons and Graphics: Design custom icons and graphics that are cohesive with the app's theme and purpose. Illustrations should be simple, relatable, and supportive of the learning process.

Target Market(s)

Educational

Industry/Entity Type

Educational

Colors
0054AA
0677BA
7BADD7
CADEEF
E8F1F8
0094D4
00A9DD
6FCCEA
C7EBF8
E9F6FB

Requirements
Must have
• Educational app, a writing area, scoring and account management
Nice to have
• Statistics, Ranking Page, Settings and some nice visual features

```html
<!DOCTYPE html>
<html lang="en">
<head>
<meta charset="utf-8">
<title>Brivonest – App Screens</title>
<link href="https://fonts.googleapis.com/css2?family=Fredoka:wght@500;700&family=Poppins:wght@400;500&family=Rosarivo&family=Special+Elite&family=Bangers&family=Rubik+Mono+One&display=swap" rel="stylesheet">
<style>
  :root{
    --brand:#0054AA;
    --brand-deep:#0a3f8f;
    --btn-a:#1474ea;
    --btn-b:#1a2c9e;
    --band-a:#1673df;
    --band-b:#0a3d85;
    --navy:#053a7a;
    --ink:#1c1c24;
    --muted:#6b6b78;
    --line:#2a4fb8;
    --sky:#6FCCEA;
    --sky-soft:#C7EBF8;
    --paper:#ffffff;
  }
  *{margin:0;padding:0;box-sizing:border-box}
  html,body{width:1200px;height:697px;overflow:hidden;background:var(--paper)}
  .stage{position:relative;width:1200px;height:697px;overflow:hidden;font-family:"Poppins",sans-serif;color:var(--ink)}
  .backdrop{position:absolute;inset:0}
  .screen{position:absolute;top:83px;width:254px;height:531px;background:var(--paper);overflow:hidden;box-shadow:0 10px 26px rgba(0,0,0,.22)}
  .screen--signup{left:128px}
  .screen--main{left:473px}
  .screen--profile{left:819px}
  .abs{position:absolute}
  .center-x{left:0;right:0;text-align:center}

  /* sign up */
  .brand-name{top:10px;font-family:"Fredoka",sans-serif;font-weight:700;font-size:37px;color:var(--brand);letter-spacing:.5px}
  .hero-art{left:38px;top:70px;width:180px;height:204px;border-radius:50% 50% 46% 46%;background:radial-gradient(circle at 50% 45%,var(--sky-soft),var(--sky) 70%,#f4c64a 100%)}
  .signup-title{top:298px;font-family:"Rosarivo",serif;font-size:16px;color:var(--ink)}
  .signup-sub{top:317px;font-size:8px;color:var(--ink)}
  .field{left:33px;top:339px;width:188px;height:25px;border:1.2px solid var(--line);border-radius:3px;font-size:7.5px;color:var(--muted);padding:7px 12px}
  .pill-btn{height:29px;border-radius:15px;background:linear-gradient(90deg,var(--btn-a),var(--btn-b));color:#fff;font-size:9px;font-weight:500;display:flex;align-items:center;justify-content:center;box-shadow:0 4px 8px rgba(20,60,170,.25)}
  .btn-email{left:33px;top:374px;width:188px}
  .divider{top:417px;left:18px;width:218px;display:flex;align-items:center;gap:8px;font-size:8.5px;color:var(--muted)}
  .divider::before,.divider::after{content:"";flex:1;height:1px;background:#8da2cc}
  .btn-alt{left:33px;top:443px;width:188px;height:29px;border:1px solid #444;border-radius:15px;display:flex;align-items:center;justify-content:center;gap:10px;font-size:9px;color:var(--ink)}
  .btn-alt .dot{width:12px;height:12px;border-radius:50%;background:var(--brand)}
  .legal{top:476px;font-size:7px;line-height:10.5px;color:var(--ink)}
  .legal a{color:#1a6fd8;text-decoration:underline}

  /* main */
  .header-wave{left:0;top:0;width:254px;height:210px}
  .menu-icon{left:19px;top:21px;width:17px;height:14px}
  .screen-title{top:17px;font-family:"Rosarivo",serif;font-size:16px;color:#fff}
  .points{left:192px;top:19px;width:55px;height:20px;border-radius:10px;background:#1a6be0;display:flex;align-items:center;justify-content:center;gap:3px;font-family:"Fredoka",sans-serif;font-size:6.5px;font-weight:500;color:#fff;box-shadow:0 0 0 1px rgba(255,255,255,.15)}
  .points i{width:7px;height:7px;border-radius:50%;background:#f5c41a}
  .canvas-area{left:0;top:60px;width:254px;height:248px;background:linear-gradient(180deg,#f6f6f6,#f2f2f2 60%,#f7f7f7);z-index:0}
  .main-head{z-index:1}
  .grip{left:114px;top:77px;width:26px;height:1px;background:#9aa8c8;z-index:2}
  .tool-icons{left:0;top:142px;width:254px;height:70px}
  .toggle{left:33px;top:325px;width:188px;height:32px;border:1.2px solid var(--line);border-radius:16px;display:flex;font-size:8px}
  .toggle span{flex:1;display:flex;align-items:center;justify-content:center;color:var(--muted)}
  .toggle .is-active{background:linear-gradient(90deg,var(--btn-a),var(--btn-b));color:#fff;border-radius:16px}
  .chip{height:28px;width:74px;border:1.2px solid var(--line);border-radius:14px;display:flex;align-items:center;justify-content:center;font-size:10px;color:var(--ink)}
  .chip-1{left:7px;top:372px;font-family:"Rosarivo",serif;font-weight:700}
  .chip-2{left:90px;top:372px;font-family:"Special Elite",serif}
  .chip-3{left:173px;top:372px;font-family:"Fredoka",sans-serif;font-weight:700}
  .chip-4{left:47px;top:411px;font-family:"Rubik Mono One",sans-serif;font-size:8px}
  .chip-5{left:133px;top:411px;font-family:"Bangers",cursive;font-size:10px}
  .btn-results{left:33px;top:470px;width:188px}

  /* profile */
  .back-icon{left:15px;top:21px;width:10px;height:14px}
  .avatar{left:97px;top:54px;width:61px;height:61px;border-radius:50%;background:radial-gradient(circle at 50% 40%,#d9d4cf,#8a8580 75%);border:1px solid rgba(255,255,255,.4);z-index:2}
  .edit-photo{top:127px;font-size:11px;color:#fff;z-index:2}
  .grip-light{left:114px;top:195px;width:26px;height:1px;background:#9aa8c8}
  .row{left:10px;right:8px;display:flex;font-size:10.5px}
  .row .label{width:77px;color:var(--ink)}
  .row .value{flex:1;color:var(--muted)}
  .row svg{width:6px;height:10px;margin-top:3px}
  .row-name{top:238px}
  .row-user{top:276px}
  .row-mail{top:316px}
  .row-links{top:356px}
  .row-bio{top:465px}
  .link-extra{left:87px;font-size:10.5px;color:var(--muted)}
</style>
</head>
<body>
<main class="stage">
  <svg class="backdrop" viewBox="0 0 1200 697" preserveAspectRatio="none" aria-hidden="true">
    <defs>
      <linearGradient id="bandGrad" x1="0" y1="1" x2="1" y2="0">
        <stop offset="0" stop-color="#1673df"/>
        <stop offset="0.6" stop-color="#0c57b8"/>
        <stop offset="1" stop-color="#053a7a"/>
      </linearGradient>
    </defs>
    <polygon points="0,593 985,0 1200,0 1200,100 208,697 0,697" fill="url(#bandGrad)"/>
  </svg>

  <!-- sign up -->
  <section class="screen screen--signup">
    <div class="abs center-x brand-name">Brivonest</div>
    <div class="abs hero-art" role="img" aria-label="Illustration of a child reading an English book among letter blocks and school supplies"></div>
    <h1 class="abs center-x signup-title" style="font-weight:400">Create an account</h1>
    <p class="abs center-x signup-sub">Enter your email to sign up for this app</p>
    <div class="abs field">Your Email Address</div>
    <div class="abs pill-btn btn-email">Sign Up With Email</div>
    <div class="abs divider">or continue with</div>
    <div class="abs btn-alt"><span class="dot"></span>Sign Up With Quarnix</div>
    <p class="abs center-x legal">By clicking continue, you agree to our<br><a>Terms of Service</a> and <a>Privacy Policy</a></p>
  </section>

  <!-- main -->
  <section class="screen screen--main">
    <div class="abs canvas-area"></div>
    <svg class="abs header-wave main-head" viewBox="0 0 254 210" aria-hidden="true">
      <path d="M0,70 C20,62 40,55 62,59 C90,64 105,85 127,86 C150,86 175,68 200,63 C225,58 240,61 254,62 V0 H0Z" fill="var(--brand)"/>
    </svg>
    <div class="abs grip"></div>
    <svg class="abs menu-icon" viewBox="0 0 17 14" style="z-index:2" aria-hidden="true">
      <path d="M0,1H17M0,7H17M0,13H17" stroke="#fff" stroke-width="2"/>
    </svg>
    <div class="abs center-x screen-title" style="z-index:2">Main Screen</div>
    <div class="abs points" style="z-index:2"><i></i>16 Points</div>
    <svg class="abs tool-icons" viewBox="0 0 254 70" aria-hidden="true">
      <g fill="none" stroke="#111" stroke-width="1.6" stroke-linecap="round" stroke-linejoin="round">
        <path d="M60,8 C75,6 88,10 80,18 C72,24 70,28 80,28"/>
        <path d="M104,14 L110,20 L72,58 L64,60 L66,52 Z"/>
        <path d="M101,17 L107,23"/>
        <path d="M66,52 L72,58"/>
        <path d="M62,62 C56,58 60,52 66,54"/>
        <path d="M190,20 C178,10 154,14 150,34 C147,50 162,62 178,58 C186,56 184,48 178,46 C172,44 178,36 188,40"/>
        <circle cx="163" cy="24" r="3.5"/><circle cx="174" cy="20" r="3.5"/>
        <circle cx="158" cy="36" r="3.5"/><circle cx="164" cy="48" r="3.5"/><circle cx="175" cy="51" r="3.5"/>
        <path d="M186,8 L192,4 L195,12 L189,14 Z"/>
        <path d="M189,14 L200,58 L196,60 L190,18"/>
      </g>
    </svg>
    <div class="abs toggle"><span>Show all Words</span><span class="is-active">Play all words</span></div>
    <div class="abs chip chip-1">Word 1</div>
    <div class="abs chip chip-2">Word 2</div>
    <div class="abs chip chip-3">Word 3</div>
    <div class="abs chip chip-4">Word 4</div>
    <div class="abs chip chip-5">WORD 5</div>
    <div class="abs pill-btn btn-results">Show me the results</div>
  </section>

  <!-- profile -->
  <section class="screen screen--profile">
    <svg class="abs header-wave" viewBox="0 0 254 210" aria-hidden="true">
      <path d="M0,188 C15,182 28,178 45,180 C75,184 100,203 127,203 C155,203 185,180 215,178 C235,177 245,180 254,180 V0 H0Z" fill="var(--brand)"/>
    </svg>
    <svg class="abs back-icon" viewBox="0 0 10 14" aria-hidden="true">
      <path d="M8,1 L2,7 L8,13" fill="none" stroke="#fff" stroke-width="1.8"/>
    </svg>
    <div class="abs center-x screen-title">Profile</div>
    <div class="abs avatar" role="img" aria-label="Profile photo of the user"></div>
    <div class="abs center-x edit-photo">Edit profile image</div>
    <div class="abs grip-light"></div>

    <div class="abs row row-name"><span class="label">Name</span><span class="value">Mira Dalton</span><svg viewBox="0 0 6 10"><path d="M1,1 L5,5 L1,9" fill="none" stroke="var(--brand)" stroke-width="1.4"/></svg></div>
    <div class="abs row row-user"><span class="label">Username</span><span class="value">@username</span><svg viewBox="0 0 6 10"><path d="M1,1 L5,5 L1,9" fill="none" stroke="var(--brand)" stroke-width="1.4"/></svg></div>
    <div class="abs row row-mail"><span class="label">Email</span><span class="value">mira@postvale.com</span><svg viewBox="0 0 6 10"><path d="M1,1 L5,5 L1,9" fill="none" stroke="var(--brand)" stroke-width="1.4"/></svg></div>
    <div class="abs row row-links"><span class="label">Links</span><span class="value">brightpage.net</span><svg viewBox="0 0 6 10"><path d="M1,1 L5,5 L1,9" fill="none" stroke="var(--brand)" stroke-width="1.4"/></svg></div>
    <div class="abs link-extra" style="top:379px">inkpath.net</div>
    <div class="abs link-extra" style="top:402px">wordnook.net</div>
    <div class="abs link-extra" style="top:424px">Add link</div>
    <div class="abs row row-bio"><span class="label" style="padding-top:3px">Bio</span><span class="value">A description of this user</span><svg viewBox="0 0 6 10"><path d="M1,1 L5,5 L1,9" fill="none" stroke="var(--brand)" stroke-width="1.4"/></svg></div>
  </section>
</main>
</body>
</html>
```